KPL Construction we build lodges in Botswana

We need a Design Layout only with Categories where we can update each projects photos.... We have a web address and a host - kpl.construction

```html
<!DOCTYPE html>
<html lang="en">
<head>
<meta charset="utf-8">
<title>KPL Construction</title>
<link rel="stylesheet" href="https://fonts.googleapis.com/css2?family=Montserrat:wght@300;400;600;700&family=Open+Sans:wght@400;600&family=Lora&display=swap">
<style>
:root{
  --teal:#4fa3a0;
  --dark:#2b2c30;
  --darker:#1e1f21;
  --ink:#222;
  --light:#f3f3f3;
  --white:#fff;
  --muted:#9a9a9a;
}
*{box-sizing:border-box;margin:0;padding:0}
html,body{width:1200px;height:3068px;overflow:hidden}
body{font-family:"Open Sans",sans-serif;color:var(--ink);background:var(--light);position:relative}
section,header{position:absolute;left:0;width:1200px}
.hero{top:0;height:600px;background:linear-gradient(180deg,#7d7d7d 0%,#b9b9b9 40%,#8a8a8a 75%,#4a4a4a 100%)}
.hero-photo{position:absolute;inset:0}
.nav{position:absolute;top:0;left:0;width:1200px;height:100px;display:flex;align-items:center;padding:0 24px}
.brand{display:flex;align-items:center;gap:10px;font-family:"Montserrat",sans-serif;font-weight:700;font-size:14px;color:var(--ink);letter-spacing:1px}
.brand-mark{width:22px;height:22px;background:var(--ink)}
.menu{position:absolute;left:600px;top:26px;display:flex;gap:6px;list-style:none}
.menu li{font-family:"Montserrat",sans-serif;font-size:12px;color:var(--white);padding:16px 14px;letter-spacing:1px}
.menu li.active{background:var(--teal)}
.cart{position:absolute;right:70px;top:42px;font-family:"Montserrat",sans-serif;font-size:12px;color:var(--white);display:flex;gap:8px;align-items:center}
.hero-title{position:absolute;top:160px;width:100%;text-align:center;font-family:"Montserrat",sans-serif;font-weight:300;color:var(--white);font-size:72px;letter-spacing:10px;line-height:1.15;text-transform:uppercase;opacity:.9}
.btn{position:absolute;left:535px;top:404px;width:130px;height:40px;background:var(--teal);color:var(--white);font-family:"Montserrat",sans-serif;font-size:11px;letter-spacing:1px;display:flex;align-items:center;justify-content:center}
.slider{top:600px;height:500px;background:linear-gradient(180deg,#1f1f1f,#2b2b2b)}
.slide{position:absolute}
.slide.side{top:160px;width:260px;height:200px;border:3px solid var(--white)}
.slide.left{left:88px;background:linear-gradient(135deg,#7a3a1a,#c87a3a)}
.slide.right{left:848px;background:linear-gradient(135deg,#a5d2cf,#e8efe9)}
.slide.main{left:388px;top:100px;width:392px;height:320px;border:6px solid #3a3a3a;background:linear-gradient(135deg,#e9e6e0,#b58a5c 70%,#5a4a3a)}
.arrow{position:absolute;top:240px}
.caption{position:absolute;top:440px;width:100%;text-align:center;color:var(--white)}
.caption h3{font-family:"Montserrat",sans-serif;font-size:13px;font-weight:600;letter-spacing:3px}
.caption p{font-family:"Lora",serif;font-style:italic;font-size:15px;margin-top:12px}
.gallery{top:1100px;height:460px;background:var(--light)}
.section-title{position:absolute;width:100%;text-align:center;font-family:"Montserrat",sans-serif;font-weight:700;font-size:34px}
.gallery .section-title{top:14px}
.gallery-frame{position:absolute;left:48px;top:60px;width:1112px;height:368px;background:#333;padding:8px;display:flex;gap:8px}
.gallery-feature{width:492px;height:352px;background:linear-gradient(135deg,#d9d2c4,#9b7a55 60%,#3a3028)}
.gallery-grid{flex:1;display:grid;grid-template-columns:repeat(3,1fr);grid-template-rows:repeat(3,1fr);gap:8px}
.gallery-grid div{background:linear-gradient(135deg,#cfc8bd,#6f6458)}
.gallery-grid div:nth-child(2n){background:linear-gradient(135deg,#e3e0d9,#8d7e6a)}
.top-gallery{top:1560px;height:360px;background:var(--dark)}
.top-gallery .section-title{top:20px;color:var(--white)}
.tile{position:absolute;top:72px;width:220px;height:216px;background:linear-gradient(180deg,#9ccf4a,#4c7d1f)}
.tile.hover{background:linear-gradient(180deg,#b0dc5c,#5d9028)}
.tile.selected{border:3px solid var(--white);background:linear-gradient(180deg,#3f5a22,#253818)}
.tile-info{position:absolute;left:14px;top:14px;color:var(--white);font-size:12px;line-height:1.6}
.tile-info strong{display:block;font-size:14px;font-weight:600}
.tile-label{position:absolute;top:306px;color:var(--white);font-family:"Montserrat",sans-serif;font-weight:700;font-size:13px}
.articles{top:1920px;height:360px;background:var(--light)}
.articles .section-title{top:14px;font-family:"Open Sans",sans-serif;font-weight:600;font-size:38px}
.article{position:absolute;top:68px;width:392px;height:292px;background:linear-gradient(180deg,#222 0%,#222 52%,#7b6a5a 52%,#3c3c3c 100%)}
.article.a2{background:linear-gradient(180deg,#6b7d95 0%,#8fa3bb 55%,#d9dde2 100%)}
.article.a3{background:linear-gradient(180deg,#3a3a3a 0%,#6b6b6b 50%,#a8902f 80%,#5a5a5a 100%)}
.article-text{position:absolute;left:28px;top:20px;width:340px;font-family:"Lora",serif;color:var(--white);font-size:18px;line-height:1.3}
.article-date{position:absolute;left:28px;top:132px;color:var(--white);font-size:10px}
.subscribe{top:2280px;height:360px;background:linear-gradient(180deg,#1a1a1a 0%,#6a6a6a 45%,#3a3a3a 75%,#1b1b1b 100%)}
.sub-icon{position:absolute;left:588px;top:106px}
.sub-title{position:absolute;top:136px;width:100%;text-align:center;color:var(--white);font-size:22px}
.sub-input{position:absolute;left:348px;top:208px;width:392px;height:40px;background:var(--white);color:var(--muted);font-size:11px;padding:13px 14px}
.sub-btn{position:absolute;left:748px;top:208px;width:112px;height:40px;background:var(--teal);color:var(--white);font-size:11px;display:flex;align-items:center;justify-content:center;letter-spacing:1px}
.contact{top:2640px;height:428px;background:var(--darker)}
.card{position:absolute;top:60px;height:148px;width:244px;background:var(--white);text-align:center;padding-top:40px}
.card h4{font-family:"Montserrat",sans-serif;font-size:10px;letter-spacing:1px;color:#666;font-weight:600}
.card .rule{width:24px;height:2px;background:var(--teal);margin:10px auto}
.card p{font-size:11px;color:var(--muted)}
.social{position:absolute;top:272px;left:564px;display:flex;gap:12px}
.social span{width:24px;height:24px;border-radius:50%;background:#444}
.copyright{position:absolute;top:352px;width:100%;text-align:center;color:#666;font-size:10px}
</style>
</head>
<body>

<header class="hero">
  <div class="hero-photo" role="img" aria-label="Misty black and white savanna with large baobab trees"></div>
  <nav class="nav">
    <div class="brand"><span class="brand-mark"></span>KPL CONSTRUCTION</div>
    <ul class="menu">
      <li class="active">HOME</li><li>GALLERY</li><li>TOP</li><li>BLOG</li><li>CONTACT</li>
    </ul>
    <div class="cart">CART
      <svg width="16" height="14" viewBox="0 0 16 14"><path d="M1 1h3l2 8h8l2-6H5" fill="none" stroke="#fff" stroke-width="1.4"/><circle cx="7" cy="12" r="1.3" fill="#fff"/><circle cx="13" cy="12" r="1.3" fill="#fff"/></svg>
    </div>
  </nav>
  <h1 class="hero-title">KPL<br>Construction</h1>
  <div class="btn">VIEW PROJECTS</div>
</header>

<section class="slider">
  <svg class="arrow" style="left:10px" width="14" height="20" viewBox="0 0 14 20"><path d="M12 2L3 10l9 8" fill="none" stroke="#777" stroke-width="3"/></svg>
  <div class="slide side left" role="img" aria-label="City typography poster"></div>
  <div class="slide main" role="img" aria-label="Bright open plan lodge living room"></div>
  <div class="slide side right" role="img" aria-label="Vintage street sign lettering"></div>
  <svg class="arrow" style="right:10px" width="14" height="20" viewBox="0 0 14 20"><path d="M2 2l9 8-9 8" fill="none" stroke="#777" stroke-width="3"/></svg>
  <div class="caption">
    <h3>CITIES &amp; TYPOGRAPHY</h3>
    <p>June 14th</p>
  </div>
</section>

<section class="gallery">
  <h2 class="section-title">GALLERY</h2>
  <div class="gallery-frame">
    <div class="gallery-feature" role="img" aria-label="Kitchen and dining area of a lodge"></div>
    <div class="gallery-grid" role="img" aria-label="Grid of lodge interior photos">
      <div></div><div></div><div></div><div></div><div></div><div></div><div></div><div></div><div></div>
    </div>
  </div>
</section>

<section class="top-gallery">
  <h2 class="section-title">TOP GALLERY</h2>
  <div class="tile" style="left:176px" role="img" aria-label="Green grass close-up"></div>
  <div class="tile hover" style="left:476px" role="img" aria-label="Green grass close-up"></div>
  <div class="tile selected" style="left:784px" role="img" aria-label="Green grass close-up">
    <div class="tile-info"><strong>Photograph</strong>Made on 31/05/11<br>Made by Kabo</div>
  </div>
  <div class="tile-label" style="left:176px">NORMAL</div>
  <div class="tile-label" style="left:476px">HOVER</div>
  <div class="tile-label" style="left:784px">SELECTED</div>
</section>

<section class="articles">
  <h2 class="section-title">Our Latest Articles</h2>
  <article class="article" style="left:0" role="img" aria-label="Hands holding a coffee cup">
    <p class="article-text">Etiam commodo convallis quis minim veniam, quis nostrud exercitation ullam.</p>
    <p class="article-date">May 27, 2015</p>
  </article>
  <article class="article a2" style="left:404px" role="img" aria-label="Person outdoors under a blue sky">
    <p class="article-text">Lorem ipsum dolor sit amet conse ctetur adipiscing elit, labore et dolore aliqua.</p>
    <p class="article-date">May 17, 2015</p>
  </article>
  <article class="article a3" style="left:808px" role="img" aria-label="Knitted yellow scarf on a coat">
    <p class="article-text">Etiam commodo convallis quis minim veniam, quis nostrud exercitation ullam.</p>
    <p class="article-date">May 07, 2015</p>
  </article>
</section>

<section class="subscribe" role="img" aria-label="Misty forest and mountain landscape">
  <svg class="sub-icon" width="24" height="22" viewBox="0 0 24 22"><path d="M1 10L23 1l-5 20-7-7-4 5v-7z" fill="#fff"/></svg>
  <p class="sub-title">Subscribe to receive updates!</p>
  <div class="sub-input">Your email address</div>
  <div class="sub-btn">SUBSCRIBE</div>
</section>

<footer>
<section class="contact">
  <div class="card" style="left:200px"><h4>ADDRESS</h4><div class="rule"></div><p>12 Lodge Road, Maun</p></div>
  <div class="card" style="left:476px"><h4>EMAIL</h4><div class="rule"></div><p>info@kpl.construction</p></div>
  <div class="card" style="left:752px"><h4>PHONE</h4><div class="rule"></div><p>+267 555 0142</p></div>
  <div class="social"><span></span><span></span><span></span></div>
  <p class="copyright">Copyright © KPL Construction 2015</p>
</section>
</footer>

</body>
</html>
```